Car transport business

We need a new business card design. Attached is our old card sample. I would just like to adjust the logo colors (blue and red) to be brighter. I changed my name to the brighter red and the word dispatcher to a brighter blue as an example. But you can adjust those colors further. And then perhaps you can use the same colors for the card design but use your imagination.

As a suggestion so the card stands out I would like to add a clip art of car carrier truck. Attached are examples of that as well

```html
<!DOCTYPE html>
<html lang="en">
<head>
<meta charset="utf-8">
<title>Northline Haul – Business Card</title>
<link href="https://fonts.googleapis.com/css2?family=Montserrat:wght@500;700;800&family=Mulish:wght@400;600&display=swap" rel="stylesheet">
<style>
  :root {
    --bg: #d9d9db;
    --brand-blue: #1570c0;
    --brand-red: #e8111b;
    --paper: #ffffff;
    --ink-white: #ffffff;
    --back-black: #1c1c1e;
    --back-dark: #262628;
    --back-grey: #8a8a8e;
    --faint-blue: #e6eef7;
  }
  * { margin: 0; padding: 0; box-sizing: border-box; }
  html, body { width: 1200px; height: 800px; overflow: hidden; background: var(--bg); }
  .canvas { position: relative; width: 1200px; height: 800px; }

  .card { position: absolute; border-radius: 18px; overflow: hidden; box-shadow: 0 10px 28px rgba(0,0,0,.18); }

  /* Front */
  .card-front { left: 120px; top: 110px; width: 340px; height: 580px; background: var(--paper); }
  .card-front .bands { position: absolute; inset: 0; }
  .front-art { position: absolute; left: 40px; top: 90px; width: 260px; height: 150px; border-radius: 80px 80px 20px 20px;
    background: radial-gradient(ellipse at center, var(--faint-blue) 0%, rgba(230,238,247,0) 70%); }
  .brand-front { position: absolute; top: 58px; left: 0; right: 0; display: flex; align-items: center; justify-content: center; gap: 10px; }
  .brand-dot { width: 14px; height: 14px; border-radius: 50%; background: var(--brand-red); }
  .brand-name { font-family: "Montserrat", sans-serif; font-weight: 800; font-size: 27px; letter-spacing: .5px; color: var(--brand-blue); text-transform: uppercase; }

  .person { position: absolute; left: 32px; top: 392px; }
  .person-name { font-family: "Montserrat", sans-serif; font-weight: 800; font-size: 30px; color: var(--brand-red); text-transform: uppercase; line-height: 1; }
  .person-role { font-family: "Mulish", sans-serif; font-size: 15px; color: var(--ink-white); margin-top: 4px; }
  .contacts { list-style: none; margin-top: 16px; }
  .contacts li { display: flex; align-items: center; gap: 9px; font-family: "Mulish", sans-serif; font-size: 14.5px; color: var(--ink-white); margin-bottom: 5px; }
  .contacts svg { width: 16px; height: 16px; flex: none; }

  /* Back */
  .card-back { left: 520px; top: 230px; width: 580px; height: 340px;
    background: linear-gradient(135deg, var(--back-dark) 0%, var(--back-black) 100%); }
  .back-art { position: absolute; left: 40px; top: 30px; width: 500px; height: 280px; border-radius: 20px;
    background: radial-gradient(ellipse at 55% 55%, #2f2f32 0%, rgba(40,40,42,0) 72%); }
  .brand-back { position: absolute; left: 0; right: 0; top: 148px; display: flex; align-items: center; justify-content: center; gap: 14px; }
  .brand-back .brand-dot { width: 18px; height: 18px; background: var(--back-grey); }
  .brand-back .brand-name { font-size: 40px; color: var(--back-grey); }
</style>
</head>
<body>
<main class="canvas">

  <section class="card card-front" aria-label="Business card front">
    <div class="front-art" role="img" aria-label="Faint outline drawing of a car"></div>
    <div class="brand-front">
      <span class="brand-dot"></span>
      <span class="brand-name">Northline Haul</span>
    </div>
    <svg class="bands" viewBox="0 0 340 580" aria-hidden="true">
      <path d="M0,300 C120,232 250,236 340,318 L340,352 C250,282 120,280 0,334 Z" fill="var(--brand-red)"/>
      <path d="M0,318 C120,262 240,262 330,330 C240,276 120,278 0,326 Z" fill="var(--brand-blue)"/>
      <path d="M0,334 C120,280 250,282 340,352 L340,580 L0,580 Z" fill="var(--brand-blue)"/>
    </svg>
    <div class="person">
      <h1 class="person-name">Dana Morrow</h1>
      <p class="person-role">Dispatcher</p>
      <ul class="contacts">
        <li><svg viewBox="0 0 16 16"><circle cx="8" cy="8" r="8" fill="var(--brand-red)"/><path d="M5.5 4.5l1.5 1.6-.8 1.1a5 5 0 0 0 2.6 2.6l1.1-.8 1.6 1.5-1 1.2C7.9 11.5 4.5 8.1 4.3 5.5z" fill="#fff"/></svg>555-014-2087</li>
        <li><svg viewBox="0 0 16 16"><circle cx="8" cy="8" r="8" fill="var(--brand-red)"/><rect x="5.5" y="3.8" width="5" height="8.4" rx="1" fill="none" stroke="#fff" stroke-width="1.2"/></svg>555-014-3391</li>
        <li><svg viewBox="0 0 16 16"><circle cx="8" cy="8" r="8" fill="var(--brand-red)"/><rect x="4" y="5" width="8" height="6" fill="none" stroke="#fff" stroke-width="1.1"/><path d="M4 5l4 3.3L12 5" fill="none" stroke="#fff" stroke-width="1.1"/></svg>hello@northlinehaul.com</li>
        <li><svg viewBox="0 0 16 16"><circle cx="8" cy="8" r="8" fill="var(--brand-red)"/><circle cx="8" cy="8" r="4" fill="none" stroke="#fff" stroke-width="1.1"/><path d="M4 8h8M8 4c-1.8 2.2-1.8 5.8 0 8M8 4c1.8 2.2 1.8 5.8 0 8" fill="none" stroke="#fff" stroke-width=".9"/></svg>www.northlinehaul.com</li>
      </ul>
    </div>
  </section>

  <section class="card card-back" aria-label="Business card back">
    <div class="back-art" role="img" aria-label="Dark tone-on-tone illustration of a car carrier truck"></div>
    <div class="brand-back">
      <span class="brand-dot"></span>
      <span class="brand-name">Northline Haul</span>
    </div>
  </section>

</main>
</body>
</html>
```